Quillfern Vaults - Direct Mailer / Flyer

We are excited to announce the launch of our new company, Quillfern Vaults, a premier cohosting facility and data center dedicated to Cryptocurrency Miners. Our website, https://quillfernvaults.example, provides detailed information about our offerings and showcases the innovative design schemes for the entire project.

Quillfern Vaults stands out in the industry by offering both GPU Hosting and ASIC Hosting services in our state-of-the-art facility, equipped with an impressive 17 Megawatts of available power. What sets us apart is our unique billing system based on actual metered power usage. We charge $0.08 for ASIC miners and $0.09 for GPU miners, ensuring cost-effectiveness and transparency for our clients.

Our commitment to excellence is evident in our use of cutting-edge technology, top-notch facilities, and strategic partnerships. These elements come together to deliver exceptional solutions tailored for real-world applications in the cryptocurrency space.

As part of our promotional efforts, we are developing a direct mailer/flyer to introduce Quillfern Vaults to a wider audience. This promotional material will also serve as a handout at events, to potential customers, and more. We welcome creative ideas and suggestions to maximize the versatility of this design and reach diverse target audiences effectively.

For a comprehensive overview of our services and to explore our design concepts, please visit https://quillfernvaults.example. Quillfern Vaults is poised to revolutionize the mining industry, and we look forward to partnering with you for success in the digital currency era.

```html
<!DOCTYPE html>
<html lang="en">
<head>
<meta charset="utf-8">
<title>Quillfern Vaults – Flyer</title>
<link rel="stylesheet" href="https://fonts.googleapis.com/css2?family=Anton&family=Poppins:wght@400;500;600;700;800&display=swap">
<style>
  :root{
    --bg:#cfcfcf;
    --paper:#ffffff;
    --ink:#1c1c1c;
    --blue:#3a4ff0;
    --card-1:#244a7d;
    --card-2:#2b78bf;
    --card-3:#0fa0d3;
    --card-4:#3bbdcb;
    --gpu-top:#cdd3fb;
    --gpu-bot:#8d9af5;
    --asic-top:#c6e7cf;
    --asic-bot:#86cb97;
    --band:#262626;
  }
  *{box-sizing:border-box;margin:0;padding:0}
  html,body{width:1200px;height:2400px;overflow:hidden}
  body{background:var(--bg);font-family:"Poppins",sans-serif;color:var(--ink);position:relative}
  .flyer{position:absolute;left:40px;top:476px;width:1120px;height:1448px;background:var(--paper);box-shadow:0 10px 30px rgba(0,0,0,.3);overflow:hidden}
  .abs{position:absolute}

  .brand{left:52px;top:56px;display:flex;align-items:center;gap:16px}
  .brand-mark{width:52px;height:52px;background:#2a2a2a;border-radius:4px}
  .brand-name{font-family:"Anton",sans-serif;font-size:52px;line-height:1;letter-spacing:1px;color:#2a2a2a;text-transform:uppercase}

  .kicker{left:52px;top:150px;font-weight:700;font-size:20px;letter-spacing:5.6px;color:var(--blue)}
  .lead-line{left:50px;top:180px;font-size:32px;font-weight:400;letter-spacing:.5px}
  .headline{left:50px;top:212px;font-family:"Anton",sans-serif;font-size:78px;line-height:1;letter-spacing:1px;color:#232323;transform:scaleY(.98)}
  .miners{left:52px;top:295px;width:322px;height:44px;background:var(--blue);color:#fff;font-weight:800;font-size:36px;letter-spacing:16px;line-height:44px;padding-left:28px}
  .intro{left:52px;top:364px;width:500px;font-size:18.5px;line-height:22px}
  .intro b{font-weight:700}

  .hero{left:570px;top:30px;width:520px;height:495px;background:radial-gradient(ellipse at 70% 55%,#d7a93a 0,#b8862a 25%,rgba(235,235,235,0) 60%),linear-gradient(180deg,#f4f4f4,#e6e6e6);border-radius:4px}

  .card{top:522px;width:210px;height:300px}
  .card-body{position:absolute;inset:0 0 10px 0;clip-path:polygon(0 0,100% 0,100% 80%,50% 100%,0 80%);color:#fff;text-align:center;padding:20px 12px 0}
  .card h3{font-weight:500;font-size:20px;margin-bottom:14px}
  .card p{font-size:18px;line-height:22px;font-weight:400}
  .card .icon{position:absolute;left:59px;top:206px;width:92px;height:92px;border-radius:50%;background:#fff;border:3px solid;display:flex;align-items:center;justify-content:center}
  .c1{left:78px}.c1 .card-body{background:var(--card-1)}.c1 .icon{border-color:var(--card-1);color:var(--card-1)}
  .c2{left:326px}.c2 .card-body{background:var(--card-2)}.c2 .icon{border-color:var(--card-2);color:var(--card-2)}
  .c3{left:574px}.c3 .card-body{background:var(--card-3)}.c3 .icon{border-color:var(--card-3);color:var(--card-3)}
  .c4{left:830px}.c4 .card-body{background:var(--card-4)}.c4 .icon{border-color:var(--card-4);color:var(--card-4)}

  .standout{left:52px;top:878px;width:420px;color:var(--blue);font-weight:700;font-size:22px;line-height:26px}
  .standout-text{left:52px;top:940px;width:460px;font-size:16.5px;line-height:20px}
  .standout-bold{left:52px;top:1002px;width:420px;font-size:16.5px;line-height:19px;font-weight:700}

  .charge-label{left:571px;top:876px;font-size:17px;font-weight:600;letter-spacing:4px}
  .price{top:903px;width:240px;height:122px;border-radius:10px;overflow:hidden;text-align:center}
  .price .name{height:48px;line-height:48px;font-weight:600;font-size:25px}
  .price .amt{height:74px;line-height:72px;font-weight:800;font-size:54px;color:#fff;border-radius:10px}
  .price-gpu{left:564px;background:var(--gpu-top)}.price-gpu .amt{background:var(--gpu-bot)}
  .price-asic{left:824px;background:var(--asic-top)}.price-asic .amt{background:var(--asic-bot)}
  .charge-note{left:568px;top:1034px;font-size:15.5px;font-weight:600}

  .band{left:49px;top:1082px;width:1019px;height:220px;background:var(--band);border-radius:14px;overflow:hidden;color:#fff}
  .band-photo{position:absolute;left:0;top:0;width:460px;height:220px;background:radial-gradient(circle at 38% 58%,#c9802d 0,#6a3d15 28%,#2d1e12 55%,var(--band) 100%)}
  .band-title{position:absolute;left:446px;top:16px;font-weight:600;font-size:17.5px}
  .pillars{position:absolute;left:446px;top:50px;width:560px;display:flex}
  .pillar{flex:1;text-align:center;font-weight:600;font-size:16.5px;line-height:19px;padding-top:2px}
  .pillar+.pillar{border-left:1px solid #555}
  .pillar:first-child{text-align:left}
  .pillar .pico{width:54px;height:54px;border-radius:50%;background:#fff;margin:0 auto 10px;display:flex;align-items:center;justify-content:center;color:var(--blue)}
  .pillar:first-child .pico{margin-left:24px}
  .band-note{position:absolute;left:446px;top:168px;font-size:16px;line-height:19px}

  .contact-label{left:52px;top:1340px;font-weight:600;font-size:20px;line-height:26px}
  .contact-label span{color:var(--blue);display:block}
  .contact-list{font-size:21px;line-height:32px;font-weight:500}
  .contact-list li{list-style:none;display:flex;align-items:center;gap:18px}
  .contact-list .ci{width:24px;height:24px;border-radius:50%;background:#222;color:#fff;display:flex;align-items:center;justify-content:center}
  .contacts-a{left:345px;top:1333px}
  .contacts-b{left:706px;top:1333px}
  .divider{left:650px;top:1336px;width:1px;height:56px;background:#bbb}
</style>
</head>
<body>
<main class="flyer">
  <div class="abs brand"><span class="brand-mark"></span><span class="brand-name">Quillfern Vaults</span></div>

  <p class="abs kicker">A PREMIER COHOSTING FACILITY</p>
  <p class="abs lead-line">DATA CENTER DEDICATED TO</p>
  <h1 class="abs headline">CRYPTOCURRENCY</h1>
  <div class="abs miners">MINERS</div>
  <p class="abs intro"><b>Quillfern Vaults has committed to leveraging</b> cutting-edge technology, state-of-the-art facilities, strategic partnerships to deliver exceptional solutions tailored for real-world applications in the cryptocurrency space.</p>

  <div class="abs hero" role="img" aria-label="Smartphone showing a crypto price chart beside stacks of gold coins"></div>

  <section class="abs card c1">
    <div class="card-body"><h3>GPU Hosting</h3><p>Begin your GPU Hosting journey with rates starting at $0.09 kWh, accepting all equipment.</p></div>
    <div class="icon"><svg width="52" height="40" viewBox="0 0 52 40" fill="none" stroke="currentColor" stroke-width="2.5"><rect x="4" y="6" width="44" height="26" rx="2"/><circle cx="18" cy="19" r="7"/><circle cx="34" cy="19" r="7"/><path d="M4 36h44M10 32v4M42 32v4"/></svg></div>
  </section>
  <section class="abs card c2">
    <div class="card-body"><h3>ASIC Hosting</h3><p>Get your ASICs directly from us or send yours in today, starting at an all-in rate of $0.08 kWh.</p></div>
    <div class="icon"><svg width="48" height="48" viewBox="0 0 48 48" fill="none" stroke="currentColor" stroke-width="2.5"><rect x="6" y="16" width="26" height="26" rx="2"/><circle cx="19" cy="29" r="7"/><path d="M26 6c8 0 14 4 16 10M34 10l-8 14"/></svg></div>
  </section>
  <section class="abs card c3">
    <div class="card-body"><h3>Mining Hardware</h3><p>Looking for mining hardware? Our equipment comes with no additional markup, ever.</p></div>
    <div class="icon"><svg width="46" height="48" viewBox="0 0 46 48" fill="none" stroke="currentColor" stroke-width="2.5"><rect x="6" y="6" width="28" height="36" rx="2"/><path d="M12 24v-6M18 24v-10M24 24v-4M12 32h16M12 37h12"/></svg></div>
  </section>
  <section class="abs card c4">
    <div class="card-body"><h3>Crypto Consulting</h3><p>Enjoy complete White Glove Services for setup, insurance, and tax consulting.</p></div>
    <div class="icon"><svg width="48" height="48" viewBox="0 0 48 48" fill="none" stroke="currentColor" stroke-width="2.5"><circle cx="20" cy="20" r="12"/><circle cx="30" cy="30" r="12"/></svg></div>
  </section>

  <h2 class="abs standout">Quillfern Vaults stands out in the industry by offering both</h2>
  <p class="abs standout-text">GPU Hosting and ASIC Hosting services in our state-of-the-art facility, equipped with an impressive 17 Megawatts of available power.</p>
  <p class="abs standout-bold">What sets us apart is our unique billing system based on actual metered power usage</p>

  <p class="abs charge-label">WE CHARGE</p>
  <div class="abs price price-gpu"><div class="name">GPU Hosting</div><div class="amt">$0.09</div></div>
  <div class="abs price price-asic"><div class="name">ASIC Hosting</div><div class="amt">$0.08</div></div>
  <p class="abs charge-note">Ensuring cost-effectiveness &amp; transparency for our clients</p>

  <section class="abs band">
    <div class="band-photo" role="img" aria-label="Miners gathered in a dim cave around a glowing gold coin"></div>
    <p class="band-title">Our commitment to excellence is evident in our use of</p>
    <div class="pillars">
      <div class="pillar"><div class="pico"><svg width="28" height="24" viewBox="0 0 28 24" fill="none" stroke="currentColor" stroke-width="2"><rect x="3" y="3" width="22" height="14" rx="1"/><path d="M9 21h10M14 17v4"/></svg></div>Cutting-edge<br>Technology</div>
      <div class="pillar"><div class="pico"><svg width="28" height="28" viewBox="0 0 28 28" fill="none" stroke="currentColor" stroke-width="2"><circle cx="14" cy="14" r="4"/><circle cx="5" cy="5" r="2.5"/><circle cx="23" cy="5" r="2.5"/><circle cx="5" cy="23" r="2.5"/><circle cx="23" cy="23" r="2.5"/><path d="M7 7l4 4M21 7l-4 4M7 21l4-4M21 21l-4-4"/></svg></div>Top-notch<br>Facilities</div>
      <div class="pillar"><div class="pico"><svg width="28" height="24" viewBox="0 0 28 24" fill="none" stroke="currentColor" stroke-width="2"><path d="M2 10l6-6 6 5 6-5 6 6-12 11z"/></svg></div>Strategic<br>Partnerships</div>
    </div>
    <p class="band-note">These elements come together to deliver exceptional solutions<br>tailored for real-world applications in the cryptocurrency space.</p>
  </section>

  <p class="abs contact-label">CONTACT US FOR<span>MORE INFORMATION</span></p>
  <ul class="abs contact-list contacts-a">
    <li><span class="ci"><svg width="12" height="12" viewBox="0 0 12 12" fill="#fff"><path d="M2 1l2.5 0 1 3-1.5 1a7 7 0 003 3l1-1.5 3 1V10a1 1 0 01-1 1A9 9 0 011 2a1 1 0 011-1z"/></svg></span>5550142268</li>
    <li><span class="ci"><svg width="12" height="14" viewBox="0 0 12 14" fill="#fff"><path d="M6 0a5 5 0 015 5c0 4-5 9-5 9S1 9 1 5a5 5 0 015-5zm0 3a2 2 0 100 4 2 2 0 000-4z"/></svg></span>Brindle Hollow, MN</li>
  </ul>
  <div class="abs divider"></div>
  <ul class="abs contact-list contacts-b">
    <li><span class="ci"><svg width="13" height="10" viewBox="0 0 13 10" fill="none" stroke="#fff" stroke-width="1.5"><rect x="1" y="1" width="11" height="8"/><path d="M1 1l5.5 4L12 1"/></svg></span>hello@quillfernvaults.example</li>
    <li><span class="ci"><svg width="14" height="14" viewBox="0 0 14 14" fill="none" stroke="#fff" stroke-width="1.3"><circle cx="7" cy="7" r="6"/><path d="M1 7h12M7 1c-3 3-3 9 0 12M7 1c3 3 3 9 0 12"/></svg></span>www.quillfernvaults.example</li>
  </ul>
</main>
</body>
</html>
```